Logo, Web and Mobile Designs for enterprise social media platform

All the details are in the attached document, please start reading the scope document first which explains what is this project about and the details about the needed deliverables, after that please read the UI_Requirements document which will detail what is expected regarding the coded web version since this is a coded contest, it is very important that you meet the UI requirements or suggest something else but we will need to agree first before working on the coded version

Good Luck

Target Market(s)

Enterprise Social Media

Industry/Entity Type

Media

Coding

Coded - Design and coding required

Number of Pages Required

5+ page

Font styles to use
Sans Serif

Requirements
Must have
• All the must haves are listed in the scope document so please check before you start

```html
<!DOCTYPE html>
<html lang="en">
<head>
<meta charset="utf-8">
<title>Teamora – Networking Tool For Entrepreneurs</title>
<link rel="stylesheet" href="https://fonts.googleapis.com/css2?family=Exo+2:wght@400;500&family=Roboto:wght@400;500;700&display=swap">
<style>
  :root {
    --header-bg: #232323;
    --brand-yellow: #ffd324;
    --accent-red: #e9564a;
    --text-dark: #555555;
    --text-light: #ffffff;
    --footer-bg: #ffffff;
    --footer-text: #666666;
    --input-bg: #ffffff;
    --placeholder: #777777;
    --arrow-bg: rgba(20, 20, 20, 0.75);
    --social-1: #3b5998;
    --social-2: #2aa3df;
    --social-3: #0e76a8;
    --social-4: #e4412b;
    --social-5: #e02a20;
    --social-6: #66a03e;
  }
  * { box-sizing: border-box; margin: 0; padding: 0; }
  html, body { width: 1200px; height: 737px; overflow: hidden; }
  body { font-family: "Roboto", Arial, sans-serif; position: relative; background: var(--footer-bg); }

  .site-header {
    position: absolute; left: 0; top: 0; width: 1200px; height: 86px;
    background: var(--header-bg);
  }
  .brand {
    position: absolute; left: 99px; top: 18px;
    font-family: "Exo 2", Arial, sans-serif; font-weight: 400;
    font-size: 40px; line-height: 48px; color: var(--brand-yellow);
  }
  .header-button {
    position: absolute; top: 22px; height: 35px;
    border-radius: 3px; font-family: "Exo 2", Arial, sans-serif;
    font-size: 12px; line-height: 33px; text-align: center;
    background: transparent; text-decoration: none;
  }
  .header-button.login { left: 954px; width: 59px; border: 1px solid #bdbdbd; color: #e0e0e0; }
  .header-button.register { left: 1024px; width: 77px; border: 1px solid var(--accent-red); color: var(--accent-red); }

  .hero {
    position: absolute; left: 0; top: 86px; width: 1200px; height: 571px;
    background:
      radial-gradient(ellipse 220px 260px at 220px 260px, rgba(190, 150, 130, 0.55), transparent 70%),
      radial-gradient(ellipse 260px 300px at 1060px 330px, rgba(40, 60, 90, 0.75), transparent 70%),
      radial-gradient(ellipse 300px 200px at 600px 150px, rgba(60, 80, 70, 0.6), transparent 70%),
      linear-gradient(180deg, #4a5a4c 0%, #3b4048 45%, #5a5c62 75%, #3c3f46 100%);
  }
  .slider-arrow {
    position: absolute; top: 226px; width: 27px; height: 34px;
    background: var(--arrow-bg);
  }
  .slider-arrow.prev { left: 0; }
  .slider-arrow.next { right: 0; }
  .slider-arrow svg { display: block; }

  .headline {
    position: absolute; left: 0; top: 122px; width: 1200px; text-align: center;
    font-family: "Exo 2", Arial, sans-serif; font-weight: 500;
    text-shadow: 0 2px 4px rgba(0, 0, 0, 0.45);
  }
  .headline .lead { display: block; font-size: 41px; line-height: 48px; color: var(--text-light); }
  .headline .focus { display: block; font-size: 45px; line-height: 50px; color: var(--brand-yellow); }

  .login-form { position: absolute; left: 412px; top: 235px; width: 375px; }
  .field {
    display: block; width: 375px; height: 53px; border: none; border-radius: 4px;
    background: var(--input-bg); padding: 0 17px;
    font-family: "Roboto", Arial, sans-serif; font-size: 13px; color: var(--placeholder);
    line-height: 53px; margin-bottom: 15px;
  }
  .form-actions { display: flex; justify-content: space-between; margin-top: 1px; }
  .form-button {
    width: 179px; height: 44px; border-radius: 3px;
    font-family: "Roboto", Arial, sans-serif; font-weight: 700; font-size: 19px;
    line-height: 44px; text-align: center;
  }
  .form-button.login { background: var(--brand-yellow); color: var(--text-dark); }
  .form-button.register { background: var(--accent-red); color: var(--text-light); }
  .form-links { display: flex; justify-content: space-between; margin-top: 10px; }
  .form-links a {
    width: 179px; text-align: center; color: var(--text-light);
    font-size: 12px; font-weight: 500; text-decoration: none;
  }

  .site-footer {
    position: absolute; left: 0; top: 657px; width: 1200px; height: 80px;
    background: var(--footer-bg);
  }
  .copyright {
    position: absolute; left: 99px; top: 32px;
    font-size: 12px; color: var(--footer-text); word-spacing: 2px;
  }
  .social-links { position: absolute; left: 896px; top: 27px; display: flex; gap: 8px; }
  .social-links span { width: 27px; height: 27px; border-radius: 50%; display: block; }
  .social-links .s1 { background: var(--social-1); }
  .social-links .s2 { background: var(--social-2); }
  .social-links .s3 { background: var(--social-3); }
  .social-links .s4 { background: var(--social-4); }
  .social-links .s5 { background: var(--social-5); }
  .social-links .s6 { background: var(--social-6); position: relative; }
  .social-links .s6 svg { position: absolute; left: 6px; top: 8px; }
</style>
</head>
<body>
  <header class="site-header">
    <div class="brand">Teamora</div>
    <a class="header-button login" href="#">Login</a>
    <a class="header-button register" href="#">Register</a>
  </header>

  <section class="hero" role="img" aria-label="Blurred photo of young entrepreneurs working with tablets, laptops and phones at a café table">
    <div class="slider-arrow prev">
      <svg width="27" height="34" viewBox="0 0 27 34"><polyline points="17,7 8,17 17,27" fill="none" stroke="#ffffff" stroke-width="1.3"/></svg>
    </div>
    <div class="slider-arrow next">
      <svg width="27" height="34" viewBox="0 0 27 34"><polyline points="10,7 19,17 10,27" fill="none" stroke="#ffffff" stroke-width="1.3"/></svg>
    </div>

    <h1 class="headline">
      <span class="lead">Networking Tool For</span>
      <span class="focus">ENTREPRENEURS</span>
    </h1>

    <form class="login-form">
      <div class="field">Email Address</div>
      <div class="field">Password</div>
      <div class="form-actions">
        <div class="form-button login">LOGIN</div>
        <div class="form-button register">REGISTER</div>
      </div>
      <div class="form-links">
        <a href="#">Forget Password?</a>
        <a href="#">Help</a>
      </div>
    </form>
  </section>

  <footer class="site-footer">
    <p class="copyright">Copyright &copy; 2015 Teamora. &nbsp;All rights reserved.</p>
    <nav class="social-links" aria-label="Social links">
      <span class="s1" aria-label="Social network 1"></span>
      <span class="s2" aria-label="Social network 2"></span>
      <span class="s3" aria-label="Social network 3"></span>
      <span class="s4" aria-label="Social network 4"></span>
      <span class="s5" aria-label="Video channel"></span>
      <span class="s6" aria-label="Email">
        <svg width="15" height="11" viewBox="0 0 15 11"><rect x="0" y="0" width="15" height="11" rx="1" fill="#ffffff"/><polyline points="0.5,0.8 7.5,6 14.5,0.8" fill="none" stroke="#66a03e" stroke-width="1.3"/></svg>
      </span>
    </nav>
  </footer>
</body>
</html>
```